Website Redesign Brief for Breezeline Climate Services WA

Creating a clear and concise brief for designers to redesign your website, https://breezelineclimatewa.com.au/, is essential to ensure the project aligns with your vision for a more energetic, friendly, optimistic, and user-friendly website. Below is a sample brief tailored to your request, balancing specificity with flexibility to allow designers to bring their creativity to the table.

Website Redesign Brief for Breezeline Climate WA
1. Project Overview

We are seeking a redesign of our website, https://breezelineclimatewa.com.au/, to create a vibrant, engaging, and user-friendly online presence that reflects our brand’s commitment to providing top-notch air conditioning services in Western Australia. The redesigned website should feel energetic, friendly, and optimistic while maintaining professionalism and improving user experience.
2. Goals and Objectives

Enhance Brand Perception: Convey a modern, approachable, and positive brand identity that resonates with both residential and commercial clients.
Improve User Experience: Simplify navigation, improve accessibility, and ensure a seamless experience across devices (desktop, tablet, mobile).
Increase Engagement: Encourage visitors to explore services, request quotes, and contact us through clear calls-to-action (CTAs).
Boost Conversion Rates: Make it easier for users to find information and take action (e.g., booking services or inquiries).
Showcase Expertise: Highlight our professional air conditioning services, experience, and customer satisfaction in an inviting way.

3. Target Audience

Primary Audience: Homeowners and small business owners in Western Australia seeking air conditioning installation, maintenance, or repair services.
Secondary Audience: Property managers, commercial clients, and real estate professionals looking for reliable HVAC solutions.
Demographics: Ages 25–65, mix of tech-savvy and non-tech-savvy users, located primarily in Perth and surrounding areas.
User Needs: Clear information about services, transparent pricing, easy contact options, and reassurance of quality and reliability.

4. Design Preferences

Tone and Style:

Energetic: Use bold, vibrant colors (e.g., blues, whites, and pops of warm tones like orange or yellow) to evoke energy and optimism.
Friendly: Incorporate approachable language, welcoming imagery, and a clean, uncluttered layout.
Optimistic: Highlight positive customer outcomes (e.g., comfort, energy savings) through visuals and messaging.
Professional yet approachable: Maintain credibility as a trusted service provider while avoiding a cold or overly corporate feel.

Visual Elements:

Use high-quality images of happy customers, comfortable homes/offices, and modern air conditioning units.
Incorporate subtle animations or micro-interactions to add energy (e.g., hover effects on buttons or smooth scrolling).
Avoid overly complex graphics that may slow down the site or distract from usability.

Typography: Clean, modern fonts that are easy to read. Use larger, bold headings for hierarchy and warmth.
Inspiration: Websites like https://www.vorlex.com.au/ (clean and professional) or https://www.tandoraclimatech.com.au/ (user-friendly and modern) but with a more vibrant and welcoming vibe.

5. Functional Requirements

User-Friendly Navigation: Simplify the menu structure to make key pages (e.g., Services, About Us, Contact) easily accessible.
Mobile Responsiveness: Ensure the site is fully optimized for mobile devices, with fast load times and intuitive touch interactions.
Key Features:

Prominent CTAs for requesting quotes, booking services, or contacting the team.
A clear service overview with icons or visuals for each service (e.g., installation, repairs, maintenance).
A testimonials section to showcase customer satisfaction.
An easy-to-use contact form with minimal fields.
Integration with plain circle Maps for location-based services or office directions.

SEO and Performance: Optimize for search engines (e.g., keywords like “air conditioning Perth”) and ensure fast loading speeds.
Accessibility: Follow WCAG guidelines to ensure the site is usable for all visitors, including those with disabilities.

6. Content Guidance

Existing Content: Review and refine current content from https://breezelineclimatewa.com.au/ to make it concise, engaging, and aligned with the friendly tone.
New Content Ideas:

Add a “Why Choose Us” section highlighting expertise, customer service, and eco-friendly solutions.
Include a FAQ page to address common customer questions.
Create a blog section for tips on air conditioning maintenance or energy efficiency (optional).

Tone of Voice: Conversational, reassuring, and positive. Avoid technical jargon unless clearly explained.

7. Technical Considerations

Platform: Open to recommendations (e.g., WordPress, Wix, or custom-built) but prioritize ease of maintenance and scalability.
Integrations: Ensure compatibility with existing tools (e.g., plain circle Analytics, CRM for quote requests, or booking systems).
Domain and Hosting: Retain current domain (breezelineclimatewa.com.au); hosting recommendations welcome.
Timeline: Initial design concepts within [insert timeline, e.g., 2–3 weeks], with full redesign completed by [insert deadline, e.g., 6–8 weeks].
Budget: [Insert budget range or state “flexible, please provide a quote”].

8. Deliverables

Wireframes and mockups for homepage, service pages, and contact page.
Fully responsive website design with all necessary pages.
Style guide (colors, fonts, imagery guidelines).
CMS setup (if applicable) with basic training for content updates.
Testing and optimization for performance and SEO.

9. Success Metrics

Increased time on site and reduced bounce rate.
Higher conversion rates for quote requests and contact form submissions.
Positive user feedback on ease of navigation and overall experience.
Improved search engine rankings for key terms within [insert timeframe, e.g., 3 months].

10. Additional Notes

Please provide a portfolio of similar projects or examples of user-friendly, vibrant websites.
We are open to creative suggestions to make the website stand out in the HVAC industry.
Regular progress updates and collaboration during the design process are appreciated.
Updates

designers are asking for more time

few have requested an extension. I Have extended

Target Market(s)

Primary Audience: Homeowners and small business owners in Western Australia seeking air conditioning installation, maintenance, or repair services. Secondary Audience: Property managers, commercial clients, and real estate professionals looking for reliable HVAC solutions. Demographics: Ages 25–65, mix of tech-savvy and non-tech-savvy users, located primarily in Perth and surrounding areas. User Needs: Clear information about services, transparent pricing, easy contact options, and reassurance of quality and reliability.

Industry/Entity Type

Air Conditioning and Refrigeration (HVAC & R)

Coding

Coded - Design and coding required

Colors
0054AA
0677BA
7BADD7
CADEEF
E8F1F8
59FF00
82FF00
B8FF75
E3FFCB
F4FFEA
F0912C
F2A743
F7CA91
FBE8D2
FDF5EE
EE7325
F08F49
F5BC92
FAE3D3
FDF4ED

Requirements
Must have
• Must have all my current information I currently have on my web page.
Nice to have
• A sales page for people to buy products online

```html
<!DOCTYPE html>
<html lang="en">
<head>
<meta charset="utf-8">
<title>Breezeline Climate Services WA</title>
<link rel="stylesheet" href="https://fonts.googleapis.com/css2?family=Poppins:wght@400;500;600;700;800&display=swap">
<style>
:root{
  --blue:#0054AA;
  --blue-mid:#0677BA;
  --blue-soft:#7BADD7;
  --blue-pale:#CADEEF;
  --blue-wash:#E8F1F8;
  --orange:#EE7325;
  --orange-warm:#F0912C;
  --orange-pale:#FBE8D2;
  --ink:#1b1f27;
  --text:#3d4450;
  --line:#d9dee6;
  --navy:#0f1a2c;
  --white:#ffffff;
}
*{box-sizing:border-box;margin:0;padding:0}
html,body{width:1200px;height:4975px;overflow:hidden}
body{position:relative;background:var(--white);font-family:"Poppins",sans-serif;color:var(--text)}
.abs{position:absolute}
.orange{color:var(--orange)}
.blue{color:var(--blue)}

/* header */
.topbar{left:0;top:0;width:1200px;height:48px;background:var(--white)}
.navbar{left:0;top:48px;width:1200px;height:43px;background:var(--orange)}
.brand{left:141px;top:0;width:162px;height:91px;background:var(--white);display:flex;align-items:center;justify-content:center;gap:6px}
.brand-dot{width:14px;height:14px;border-radius:50%;background:var(--orange);flex:none}
.brand-name{font-size:12px;font-weight:700;color:var(--orange);line-height:1.15;width:110px}
.topmail{left:555px;top:14px;display:flex;align-items:center;gap:6px;font-size:10.5px;color:var(--ink)}
.topmail b{font-weight:600}
.mail-ico{width:20px;height:20px;border-radius:50%;background:var(--blue);display:flex;align-items:center;justify-content:center}
.socials{left:830px;top:13px;display:flex;gap:14px}
.socials span{width:22px;height:22px;border-radius:50%;background:var(--blue);display:block}
.nav{left:340px;top:48px;height:43px;display:flex;align-items:center;gap:0}
.nav a{color:var(--white);text-decoration:none;font-size:15px;width:126px;text-align:center}
.callblock{left:976px;top:0;width:224px;height:91px;background:var(--blue)}
.callblock-wedge{left:976px;top:0;width:40px;height:91px}
.call-label{left:1042px;top:16px;font-size:12px;color:var(--blue-pale);display:flex;gap:6px;align-items:center}
.call-number{left:1026px;top:44px;font-size:23px;font-weight:600;color:var(--white)}

/* hero */
.hero{left:0;top:91px;width:1200px;height:531px;background:linear-gradient(90deg,#1e2632 0%,#3a4555 40%,#7d8a98 75%,#9aa5b0 100%)}
.hero-title{left:141px;top:188px;font-size:43px;font-weight:700;line-height:64px;color:var(--white);letter-spacing:.5px}
.hero-text{left:141px;top:384px;width:480px;font-size:13px;line-height:23px;color:#e9edf2}
.btn{display:flex;align-items:center;justify-content:center;font-size:11.5px;font-weight:600;text-transform:uppercase;letter-spacing:.3px}
.btn-white{left:141px;top:467px;width:139px;height:36px;background:var(--white);color:var(--ink)}
.btn-orange{left:296px;top:467px;width:143px;height:36px;background:var(--orange);color:var(--white)}
.hero-notch{left:549px;top:600px;width:102px;height:52px}

/* section heads */
.kicker{font-size:17px;font-weight:700;color:var(--ink);text-transform:uppercase;letter-spacing:.2px}
.center{left:0;width:1200px;text-align:center}
.sub{font-size:12.5px;color:var(--text)}

/* about */
.photo{background:linear-gradient(135deg,#c9d3dd,#e6ebf0 60%,#b5c2cf);border-radius:16px}
.about-kicker{left:622px;top:760px;font-size:16px}
.about-title{left:622px;top:794px;font-size:28px;font-weight:600;line-height:38px;color:var(--blue-mid)}
.about-quote{left:622px;top:890px;padding-left:13px;border-left:3px solid var(--blue);font-size:12.5px;font-weight:500;line-height:20px;color:var(--ink);width:400px}
.about-text{left:622px;top:946px;width:410px;font-size:12.5px;line-height:20.5px}
.btn-sched{background:var(--orange);color:var(--white);font-size:12px;font-weight:600;border-radius:3px;display:flex;align-items:center;justify-content:center}

/* service cards */
.svc-card{width:282px;border:2px solid var(--line);border-radius:6px;background:var(--white);padding:22px 20px}
.svc-card.active{background:linear-gradient(135deg,var(--blue-mid),var(--blue));border-color:var(--blue)}
.svc-icon{width:42px;height:42px;margin-bottom:26px}
.svc-title{font-size:14.5px;font-weight:500;color:var(--ink);line-height:22px}
.svc-title span{color:var(--blue-mid)}
.svc-text{font-size:12px;line-height:20px;margin-top:10px}
.svc-card.active .svc-title,.svc-card.active .svc-title span,.svc-card.active .svc-text{color:var(--white)}
.btn-outline{border:2px solid var(--blue-mid);color:var(--blue);background:var(--white);font-size:12px;font-weight:600;border-radius:3px;display:flex;align-items:center;justify-content:center}

/* why */
.why{left:0;top:1926px;width:1200px;height:620px;background:var(--blue-wash)}
.why-photo{left:149px;top:2085px;width:436px;height:380px;border-radius:14px;background:linear-gradient(135deg,#9aa8b4,#dfe5ea 45%,#e2863f 80%,#c86a2a)}
.callbox{left:153px;top:2374px;width:222px;height:85px;border-radius:10px;background:linear-gradient(135deg,var(--orange-warm),var(--orange));display:flex;align-items:center;gap:14px;padding-left:26px}
.callbox-ico{width:40px;height:40px;border-radius:50%;border:2px solid rgba(255,255,255,.6);display:flex;align-items:center;justify-content:center}
.callbox small{display:block;font-size:11px;color:var(--white);letter-spacing:.4px}
.callbox strong{display:block;font-size:17px;color:var(--white);font-weight:600}
.step-line{left:657px;top:2160px;height:230px;border-left:2px dashed var(--blue-soft)}
.step{left:628px;display:flex;gap:22px}
.step-num{width:58px;height:58px;border-radius:50%;background:var(--white);border:2px solid var(--blue-mid);display:flex;align-items:center;justify-content:center;font-size:19px;font-weight:600;color:var(--blue);flex:none}
.step-num.filled{background:var(--blue);color:var(--white);box-shadow:0 0 0 5px var(--blue-pale)}
.step h4{font-size:15px;font-weight:600;color:var(--ink);margin-top:0;margin-bottom:6px}
.step p{font-size:12px;line-height:20px;width:330px}

/* brands */
.brands{left:0;top:2546px;width:1200px;height:358px;background:linear-gradient(135deg,var(--blue-mid),var(--blue) 70%)}
.brand-badge{top:2732px;width:168px;height:69px;background:var(--white);border-radius:4px;display:flex;align-items:center;justify-content:center}
.brand-badge i{display:block;width:110px;height:22px;border-radius:3px;background:var(--blue-pale)}
.brand-badge i.red{background:#f3c7c7}
.pager{display:flex;align-items:center;gap:22px}
.pager b{display:flex;gap:4px}
.pager b span{width:6px;height:6px;border-radius:50%;background:var(--blue-soft)}
.pager b span.on{background:var(--orange)}

/* video */
.video-bg{left:0;top:2904px;width:1200px;height:516px;background-image:radial-gradient(circle,#dfe6ee 1.6px,transparent 1.8px);background-size:22px 22px}
.video-frame{left:141px;top:2985px;width:916px;height:386px;background:var(--white);box-shadow:0 8px 30px rgba(20,40,70,.15);padding:10px}
.video-image{width:100%;height:100%;background:linear-gradient(120deg,#e9ecef,#c8d0d8 45%,#7a8a9c 80%,#56677a)}
.play{left:571px;top:3150px;width:56px;height:56px;border-radius:50%;background:var(--white);display:flex;align-items:center;justify-content:center}

/* reviews */
.review{top:3549px;width:282px;height:276px;border:2px solid var(--line);border-radius:6px;background:var(--white);padding:22px 14px 0}
.review p{font-size:11.6px;line-height:21px;color:var(--text);height:100px}
.review h5{font-size:13.5px;font-weight:500;color:var(--orange);margin-top:20px}
.review .role{font-size:11.5px;color:var(--ink)}
.review .qmark{right:18px;top:146px;font-size:56px;font-weight:800;line-height:1;color:var(--orange)}
.review .qmark.b{color:var(--blue)}
.review .foot{left:0;bottom:0;width:100%;height:60px;border-top:1px solid var(--line);display:flex;align-items:center;justify-content:space-between;padding:0 14px;font-size:11.5px;color:var(--ink)}
.review .gcirc{left:126px;top:-13px;width:26px;height:26px;border-radius:50%;background:var(--white);border:1px solid var(--line)}
.stars{color:#f5b400;font-size:15px;letter-spacing:1px}

/* quote */
.quote{left:0;top:3941px;width:1200px;height:642px;background:var(--blue-wash)}
.quote-title{left:141px;top:4028px;font-size:21px;font-weight:700;color:var(--ink)}
.field{background:var(--white);border:1px solid #e0e5ec;font-size:12px;color:var(--ink);padding:0 15px;display:flex;align-items:center}
.field.area{align-items:flex-start;padding-top:14px}
.btn-send{left:141px;top:4461px;width:197px;height:42px;background:var(--blue);color:var(--white);font-size:12.5px;font-weight:600;display:flex;align-items:center;justify-content:center;gap:8px}
.quote-photo{left:638px;top:4024px;width:419px;height:483px;border-radius:12px;background:linear-gradient(180deg,#e7ebef 0%,#b4bfca 45%,#3d4c60 80%,#2a3646 100%)}
.info-row{left:672px;display:flex;gap:12px;color:var(--white)}
.info-row h6{font-size:13px;font-weight:500}
.info-row p{font-size:13px;line-height:23px;color:#eef2f6}

/* footer */
.footer{left:0;top:4583px;width:1200px;height:392px;background:var(--navy)}
.foot-brand{left:108px;top:4700px;display:flex;align-items:center;gap:8px}
.foot-brand span.dot{width:16px;height:16px;border-radius:50%;background:var(--orange)}
.foot-brand b{font-size:16px;font-weight:700;color:var(--orange);width:170px;line-height:1.2}
.foot-col h4{font-size:15px;font-weight:600;color:var(--orange);margin-bottom:12px}
.foot-col li{list-style:none;font-size:12.5px;color:#e4e8ef;line-height:18px;margin-bottom:11px;padding-left:11px;position:relative}
.foot-col li::before{content:"›";position:absolute;left:0;top:-1px;color:var(--orange);font-weight:700}
.contact-line{display:flex;gap:14px;align-items:center;font-size:12.5px;color:#e4e8ef;line-height:20px;margin-bottom:18px}
.contact-ico{width:30px;height:30px;border-radius:50%;background:#2a3447;display:flex;align-items:center;justify-content:center;flex:none}
.contact-ico.hot{background:var(--orange)}
.copy-rule{left:0;top:4936px;width:1200px;border-top:1px solid #26324a}
.copy{left:110px;top:4949px;font-size:10.5px;color:#c6ccd6}
.copy-social{left:985px;top:4950px;display:flex;gap:10px}
.copy-social span{width:12px;height:12px;background:#e4e8ef;border-radius:50%}
</style>
</head>
<body>

<!-- header -->
<div class="abs topbar"></div>
<div class="abs navbar"></div>
<div class="abs brand"><span class="brand-dot"></span><span class="brand-name">Breezeline Climate WA</span></div>
<div class="abs topmail"><span class="mail-ico"><svg width="11" height="9" viewBox="0 0 11 9"><rect x=".5" y=".5" width="10" height="8" fill="none" stroke="#fff"/><path d="M.5 .5 5.5 5 10.5 .5" fill="none" stroke="#fff"/></svg></span><span><b>EMAIL :</b> info@breezelineclimatewa.com</span></div>
<div class="abs socials"><span></span><span></span><span></span><span></span></div>
<nav class="abs nav"><a>Home</a><a>Services</a><a>About</a><a>Regasing</a><a>Contact</a></nav>
<div class="abs callblock"></div>
<svg class="abs callblock-wedge" viewBox="0 0 40 91" preserveAspectRatio="none"><path d="M0 91 L0 40 Q0 0 40 0 L40 10 Q12 12 10 48 L10 91Z" fill="#EE7325"/></svg>
<div class="abs call-label"><svg width="14" height="14" viewBox="0 0 24 24"><circle cx="12" cy="12" r="11" fill="none" stroke="#CADEEF" stroke-width="2"/><path d="M8 7c0 5 4 9 9 9l1-2-3-1-1 1c-2-1-3-2-4-4l1-1-1-3z" fill="#CADEEF"/></svg>Call Us Today</div>
<div class="abs call-number">0400 555 182</div>

<!-- hero -->
<div class="abs hero" role="img" aria-label="Technician in a blue uniform fitting a ceiling air conditioning unit"></div>
<h1 class="abs hero-title">ON DEMAND <span class="orange">HVAC</span><br><span class="orange">EXPERTISE</span> ALWAYS<br>READY TO SERVE</h1>
<p class="abs hero-text">Providing reliable installation, maintenance, and repair services for homes across Western Australia.</p>
<div class="abs btn btn-white">Get Started</div>
<div class="abs btn btn-orange">Request Service</div>
<svg class="abs hero-notch" viewBox="0 0 102 52"><path d="M0 22 L40 48 Q51 55 62 48 L102 22 L102 0 L0 0Z" fill="#4a5563"/><path d="M43 16l8 6 8-6M43 24l8 6 8-6" fill="none" stroke="#fff" stroke-width="2.5"/></svg>

<!-- about -->
<div class="abs photo" style="left:141px;top:728px;width:207px;height:205px" role="img" aria-label="Technician servicing a wall air conditioner"></div>
<div class="abs photo" style="left:367px;top:728px;width:207px;height:205px" role="img" aria-label="Technician checking an outdoor condenser unit"></div>
<div class="abs photo" style="left:141px;top:951px;width:433px;height:205px;background:linear-gradient(180deg,#9cc1e6 0%,#cfe0ef 40%,#e9edf0 55%,#8fa06a 100%)" role="img" aria-label="Row of outdoor air conditioning condensers"></div>
<div class="abs kicker about-kicker">About Us</div>
<h2 class="abs about-title">Quality AC Repair Service With<br><span class="orange">Quality Repair Solutions</span></h2>
<p class="abs about-quote">Experience Ultimate Comfort with Perth's Most Trusted Air Conditioning Experts</p>
<p class="abs about-text">Our service is second to none; our team of experienced technicians that consistently deliver the best quality air conditioner repairs Perth has to offer. There are many different brands of air conditioning on the market, each with their own way of controlling the temperature of your home.</p>
<div class="abs btn-sched" style="left:622px;top:1090px;width:161px;height:36px">Schedule a Service</div>

<!-- services -->
<div class="abs center kicker" style="top:1270px">Our <span class="blue">Services</span></div>
<p class="abs center sub" style="top:1304px">Discover what makes us the preferred choice for air conditioning services in Perth</p>

<div class="abs svc-card" style="left:141px;top:1347px;height:193px">
  <svg class="svc-icon" viewBox="0 0 42 42" fill="none" stroke="#0054AA" stroke-width="2"><rect x="4" y="26" width="34" height="10" rx="2"/><circle cx="21" cy="14" r="10"/><path d="M14 7l14 14"/></svg>
  <div class="svc-title">Commercial air conditioner <span>Installation &amp; Services</span></div>
  <div class="svc-text">There are many variations passages of Lorem Ipsum available.</div>
</div>
<div class="abs svc-card active" style="left:458px;top:1347px;height:193px">
  <svg class="svc-icon" viewBox="0 0 42 42" fill="none" stroke="#fff" stroke-width="2"><rect x="4" y="12" width="34" height="24" rx="3"/><circle cx="16" cy="24" r="7"/><path d="M28 18h6M28 24h6M28 30h6M12 6h18"/></svg>
  <div class="svc-title">Domestic air conditioner <span>Installation &amp; Services</span></div>
  <div class="svc-text">There are many variations passages of Lorem Ipsum available.</div>
</div>
<div class="abs svc-card" style="left:775px;top:1347px;height:193px">
  <svg class="svc-icon" viewBox="0 0 42 42" fill="none" stroke="#0054AA" stroke-width="2"><circle cx="21" cy="12" r="7"/><path d="M8 38v-8h26v8M4 24h34"/></svg>
  <div class="svc-title">Coolroom Installation &amp; <span>Repairs</span></div>
  <div class="svc-text">There are many variations passages of Lorem Ipsum available.</div>
</div>
<div class="abs svc-card" style="left:141px;top:1577px;height:177px">
  <svg class="svc-icon" viewBox="0 0 42 42" fill="none" stroke="#0054AA" stroke-width="2"><path d="M8 34l10-10M14 6l-4 10h8l-4 10M28 6l-4 10h8l-4 10M22 36h16"/></svg>
  <div class="svc-title">Chiller Service &amp; Repairs</div>
  <div class="svc-text">There are many variations passages of Lorem Ipsum available.</div>
</div>
<div class="abs svc-card" style="left:458px;top:1577px;height:177px">
  <svg class="svc-icon" viewBox="0 0 42 42" fill="none" stroke="#0054AA" stroke-width="2"><path d="M6 6h28v10M12 16h22M20 16v20M12 22l8-6"/></svg>
  <div class="svc-title">Air Quality Control</div>
  <div class="svc-text">There are many variations passages of Lorem Ipsum available.</div>
</div>
<div class="abs svc-card" style="left:775px;top:1577px;height:177px">
  <svg class="svc-icon" viewBox="0 0 42 42" fill="none" stroke="#0054AA" stroke-width="2"><circle cx="18" cy="14" r="8"/><path d="M6 38c0-8 6-12 12-12s12 4 12 12M30 6l6 6-6 6"/></svg>
  <div class="svc-title">BMS Upgrades &amp; Installation</div>
  <div class="svc-text">There are many variations passages of Lorem Ipsum available.</div>
</div>

<div class="abs btn-sched" style="left:429px;top:1806px;width:154px;height:35px">Schedule a Service</div>
<div class="abs" style="left:599px;top:1814px;font-size:12px;font-weight:600;color:var(--ink)">Or</div>
<div class="abs btn-outline" style="left:629px;top:1806px;width:140px;height:35px">Message Us Now</div>

<!-- why choose -->
<div class="abs why"></div>
<div class="abs center kicker" style="top:2006px">Why Choose <span class="blue">Breezeline Climate WA</span></div>
<p class="abs center sub" style="top:2040px">Discover what makes us the preferred choice for air conditioning services in Perth</p>
<div class="abs why-photo" role="img" aria-label="Technician in a yellow hard hat servicing an outdoor condenser unit"></div>
<div class="abs callbox">
  <span class="callbox-ico"><svg width="16" height="16" viewBox="0 0 24 24"><path d="M5 3c0 9 7 16 16 16l1-4-5-2-2 2c-3-1-5-3-6-6l2-2-2-5z" fill="#fff"/></svg></span>
  <span><small>CALL NOW</small><strong>0400 555 182</strong></span>
</div>
<div class="abs step-line"></div>
<div class="abs step" style="top:2119px"><span class="step-num filled">01</span><div><h4>Prompt Service</h4><p>We value your time. Our technicians arrive on schedule and work efficiently to minimize disruption to your day.</p></div></div>
<div class="abs step" style="top:2243px"><span class="step-num">02</span><div><h4>Eco-Friendly Solutions</h4><p>Our energy-efficient systems reduce your carbon footprint while saving you money on energy bills.</p></div></div>
<div class="abs step" style="top:2367px"><span class="step-num">03</span><div><h4>24/7 Support</h4><p>Emergency services available when you need them most. We're here for you around the clock.</p></div></div>

<!-- brands -->
<div class="abs brands"></div>
<div class="abs center kicker" style="top:2624px;color:#fff">Our Services</div>
<p class="abs center sub" style="top:2658px;color:#e3ecf6;line-height:20px">Please Be aware that paying for your service upfront does not mean next day service. Your service<br>will however be prioritised and scheduled into the next available slot.</p>
<div class="abs brand-badge" style="left:124px"><i class="red"></i></div>
<div class="abs brand-badge" style="left:301px"><i></i></div>
<div class="abs brand-badge" style="left:507px"><i></i></div>
<div class="abs brand-badge" style="left:721px"><i></i></div>
<div class="abs brand-badge" style="left:916px"><i class="red"></i></div>
<div class="abs pager" style="left:553px;top:2828px;color:#fff;font-size:15px"><span>←</span><b><span></span><span class="on"></span><span></span></b><span>→</span></div>

<!-- video -->
<div class="abs video-bg"></div>
<div class="abs video-frame"><div class="video-image" role="img" aria-label="Technician reaching up to service a split system air conditioner"></div></div>
<div class="abs play"><svg width="18" height="20" viewBox="0 0 18 20"><path d="M2 1l15 9-15 9z" fill="#EE7325"/></svg></div>

<!-- reviews -->
<div class="abs center kicker" style="top:3476px">What Our Customers <span class="blue">Say</span></div>
<p class="abs center sub" style="top:3508px">Don't just take our word for it - hear from our satisfied clients</p>

<div class="abs review" style="left:141px">
  <p>Breezeline Climate WA installed our new ducted system and we couldn't be happier. The team was professional, punctual and cleaned up perfectly after</p>
  <h5>Leah Morton</h5><div class="role">Homeowner, Subiaco</div>
  <span class="abs qmark">“</span>
  <div class="abs foot"><span class="abs gcirc"></span><span>450+ Review</span><span class="stars">★★★★★</span></div>
</div>
<div class="abs review" style="left:458px">
  <p>I've been using their maintenance service for three years now. They're always thorough, polite, and reasonably priced. My energy bills have decreased since they optimized my system.</p>
  <h5>Daniel Osei</h5><div class="role">Business Owner, Perth CBD</div>
  <span class="abs qmark b">“</span>
  <div class="abs foot"><span class="abs gcirc"></span><span>450+ Review</span><span class="stars">★★★★★</span></div>
</div>
<div class="abs review" style="left:775px">
  <p>Breezeline Climate WA installed our new ducted system and we couldn't be happier. The team was professional, punctual and cleaned up perfectly after</p>
  <h5>Grant Whitby</h5><div class="role">Property Manager, Joondalup</div>
  <span class="abs qmark">“</span>
  <div class="abs foot"><span class="abs gcirc"></span><span>450+ Review</span><span class="stars">★★★★★</span></div>
</div>
<div class="abs pager" style="left:553px;top:3854px;color:var(--ink);font-size:15px"><span>←</span><b><span></span><span class="on" style="background:var(--blue)"></span><span></span></b><span>→</span></div>

<!-- quote -->
<div class="abs quote"></div>
<h2 class="abs quote-title">GET YOUR <span class="orange">FREE QUOTE</span></h2>
<p class="abs sub" style="left:141px;top:4066px;font-size:12px">Lorem Ipsum Is Simply Dummy Text Of The Printing</p>
<div class="abs field" style="left:141px;top:4105px;width:216px;height:41px">Name</div>
<div class="abs field" style="left:381px;top:4105px;width:218px;height:41px">Phone</div>
<div class="abs field" style="left:141px;top:4167px;width:458px;height:41px">Email</div>
<div class="abs field" style="left:141px;top:4227px;width:458px;height:41px;justify-content:space-between">Service Phases<svg width="10" height="6" viewBox="0 0 10 6"><path d="M1 1l4 4 4-4" fill="none" stroke="#1b1f27" stroke-width="1.4"/></svg></div>
<div class="abs field area" style="left:141px;top:4289px;width:458px;height:129px">Tell us about your truck and what you're looking for...</div>
<div class="abs btn-send">Send Message <svg width="14" height="14" viewBox="0 0 14 14"><path d="M1 7l12-6-4 12-2-5z" fill="#fff"/></svg></div>
<div class="abs quote-photo" role="img" aria-label="Technician on a ladder installing a wall air conditioner"></div>
<div class="abs info-row" style="top:4322px"><svg width="16" height="16" viewBox="0 0 24 24"><path d="M5 3c0 9 7 16 16 16l1-4-5-2-2 2c-3-1-5-3-6-6l2-2-2-5z" fill="#fff"/></svg><div><h6>Phone</h6><p>0400 555 182</p></div></div>
<div class="abs info-row" style="top:4386px"><svg width="16" height="16" viewBox="0 0 24 24"><circle cx="12" cy="12" r="10" fill="#fff"/><path d="M12 6v6l4 2" fill="none" stroke="#3d4c60" stroke-width="2"/></svg><div><h6>Working Hours</h6><p>Mon–Fri: 8.00am to 5.00pm<br>Weekends and Public Holidays:<br>Additional Callout Fee.</p></div></div>

<!-- footer -->
<footer class="abs footer"></footer>
<div class="abs foot-brand"><span class="dot"></span><b>Breezeline Climate WA</b></div>
<div class="abs foot-col" style="left:354px;top:4660px"><h4>Quick Links</h4><ul><li>Home</li><li>About</li><li>Service</li><li>Project Works</li><li>Residential Services</li><li>Contact</li></ul></div>
<div class="abs foot-col" style="left:564px;top:4660px;width:210px"><h4>Services</h4><ul><li>Commercial air conditioner Installation &amp; Services</li><li>Domestic air conditioner Installation &amp; Services</li><li>Coolroom &nbsp;Repairs</li><li>Chiller Service &amp; Repairs</li><li>Air Quality Control</li><li>BMS Upgrades &amp; Installation</li></ul></div>
<div class="abs foot-col" style="left:825px;top:4660px;width:300px">
  <h4>Contact Us</h4>
  <div class="contact-line" style="margin-top:16px"><span class="contact-ico"><svg width="12" height="14" viewBox="0 0 12 14"><path d="M6 13C2 8 1 6 1 5a5 5 0 0110 0c0 1-1 3-5 8z" fill="none" stroke="#fff" stroke-width="1.4"/><circle cx="6" cy="5" r="1.6" fill="#fff"/></svg></span><span>58 Tindal Road, Banjup<br>WA 6164</span></div>
  <div class="contact-line"><span class="contact-ico hot"><svg width="13" height="13" viewBox="0 0 24 24"><path d="M5 3c0 9 7 16 16 16l1-4-5-2-2 2c-3-1-5-3-6-6l2-2-2-5z" fill="#fff"/></svg></span><span>Phone: 0400 555 182</span></div>
  <div class="contact-line"><span class="contact-ico"><svg width="13" height="10" viewBox="0 0 13 10"><rect x=".5" y=".5" width="12" height="9" fill="none" stroke="#fff"/><path d="M.5 .5l6 5 6-5" fill="none" stroke="#fff"/></svg></span><span>info@breezelineclimatewa.com.au</span></div>
</div>
<div class="abs copy-rule"></div>
<div class="abs copy">Copyright © 2025 Breezeline Climate Services WA All Right Reserved AU40217 &nbsp;Terms &amp; Conditions Privacy Policy Contact Us</div>
<div class="abs copy-social"><span></span><span></span><span></span></div>

</body>
</html>
```